Kestrada LLC, needs a web page no more than 5 pages (for now)

Kestrada is a general contractor. Our services include general contracting, design-build construction, disaster recovery and environmental remediation. Our main clients are PMX, TQ, State and Local Gov't Agencies, Hospitals and Schools. Kestrada is also a SDVOSB.

```html
<!DOCTYPE html>
<html lang="en">
<head>
<meta charset="utf-8">
<title>Kestrada LLC — General Contracting</title>
<link rel="stylesheet" href="https://fonts.googleapis.com/css2?family=Montserrat:wght@400;500;600;700;800&display=swap">
<style>
:root{
  --gold:#c9a33e;
  --gold-light:#e6c869;
  --gold-dark:#a9822a;
  --ink:#151515;
  --ink-2:#222222;
  --text:#3a3a3a;
  --muted:#8a8a8a;
  --white:#ffffff;
  --font:'Montserrat', Arial, sans-serif;
}
*{box-sizing:border-box;margin:0;padding:0}
html,body{width:1200px;height:4372px;overflow:hidden}
body{font-family:var(--font);color:var(--text);background:var(--white);position:relative}
section,header,footer{position:relative;width:1200px;overflow:hidden}
.abs{position:absolute}
.photo{position:absolute}
.btn-gold{display:inline-block;background:linear-gradient(90deg,var(--gold-dark),var(--gold-light));color:var(--ink);font-weight:700;font-size:15px;letter-spacing:1px;padding:14px 34px;border-radius:30px}

/* Header / hero */
.hero{height:780px;background:var(--ink)}
.hero-photo{left:0;top:0;width:1200px;height:780px;background:linear-gradient(115deg,#3d3b36 0%,#6f6658 35%,#8d8676 55%,#b9b3a6 80%,#d8d4cc 100%)}
.hero-shade{left:0;top:0;width:1200px;height:780px;background:linear-gradient(180deg,rgba(0,0,0,.55),rgba(0,0,0,.15) 60%,rgba(0,0,0,0))}
.brand{left:56px;top:30px;font-size:30px;font-weight:800;color:var(--white);letter-spacing:2px}
.brand-mark{display:inline-block;width:12px;height:12px;background:var(--gold);border-radius:50%;margin-left:8px;vertical-align:middle}
.nav{left:340px;top:40px;display:flex;gap:32px;align-items:center}
.nav a{color:var(--white);text-decoration:none;font-size:14px;font-weight:600;letter-spacing:1px;white-space:nowrap}
.nav a.active{color:var(--gold);border:2px solid var(--gold);padding:8px 16px}
.phone-pill{left:952px;top:38px;background:linear-gradient(90deg,var(--gold-dark),var(--gold-light));color:var(--ink);font-weight:700;font-size:15px;padding:11px 22px;border-radius:26px;display:flex;align-items:center;gap:10px;white-space:nowrap}
.hero-title{left:0;top:180px;width:1200px;text-align:center;font-size:56px;font-weight:800;line-height:1.15;letter-spacing:1px}
.hero-title .gold{color:var(--gold)}
.hero-title .white{color:var(--white)}
.hero-sub{left:0;top:335px;width:1200px;text-align:center;color:var(--white);font-size:20px;font-weight:500}
.hero-cta{left:0;top:382px;width:1200px;text-align:center}
.hero-cta .btn-gold{padding:10px 26px;font-size:14px}
.hero-curve{left:0;top:560px}

/* About */
.about{height:540px;background:var(--white)}
.about-photo{left:100px;top:50px;width:440px;height:420px;background:linear-gradient(160deg,#8b7e6a,#b4a489 50%,#d9cfbd)}
.about-badge{left:420px;top:380px;width:120px;height:120px;border-radius:50%;background:#f1ece1;border:6px solid var(--white);box-shadow:0 4px 14px rgba(0,0,0,.25)}
.about-body{left:632px;top:50px;width:530px}
.about h2{font-size:48px;font-weight:800;color:var(--ink);letter-spacing:1px;margin-bottom:20px;line-height:1.2}
.about h2 span{color:var(--gold)}
.about p{font-size:18px;line-height:1.5;color:var(--text);margin-bottom:20px}
.about .quote-block{border-left:4px solid var(--gold);padding-left:20px;font-size:17px}

/* Services */
.services{height:560px;background:linear-gradient(180deg,#c69f3b 0%,#e2c46c 50%,#c9a33e 100%)}
.section-title{text-align:center;font-size:48px;font-weight:800;letter-spacing:1px}
.services .section-title{position:absolute;left:0;top:70px;width:1200px;color:var(--white)}
.title-rule{position:absolute;left:560px;top:140px;width:80px;height:3px;background:var(--white)}
.service-card{position:absolute;top:212px;height:310px;width:276px;overflow:hidden}
.service-card .shade{position:absolute;left:0;bottom:0;width:100%;height:60%;background:linear-gradient(180deg,rgba(0,0,0,0),rgba(0,0,0,.85))}
.service-card h3{position:absolute;left:0;bottom:24px;width:100%;text-align:center;color:var(--white);font-size:20px;font-weight:800;line-height:1.25}
.service-feature{position:absolute;left:320px;top:152px;width:282px;height:390px;background:var(--ink);box-shadow:0 10px 30px rgba(0,0,0,.4);text-align:center;padding-top:36px;z-index:2}
.feature-icon{width:92px;height:92px;border-radius:50%;margin:0 auto 18px;background:linear-gradient(135deg,var(--gold-dark),var(--gold-light));display:flex;align-items:center;justify-content:center}
.service-feature h3{color:var(--white);font-size:21px;font-weight:800;line-height:1.25;margin-bottom:14px}
.service-feature p{color:#cfcfcf;font-size:14px;line-height:1.5;padding:0 34px;margin-bottom:20px}
.service-feature .btn-gold{font-size:13px;padding:9px 26px}

/* Testimonials */
.testimonials{height:880px;background:var(--ink)}
.testi-bg{left:0;top:0;width:1200px;height:880px;background:linear-gradient(180deg,#1b1b1b,#111)}
.testimonials .section-title{position:absolute;left:0;top:236px;width:1200px;color:var(--white)}
.testimonials .section-title span{color:var(--gold)}
.testi-card{left:160px;top:312px;width:900px;height:430px;background:#1e1e1e;border:1px solid #3a3a3a}
.corner{position:absolute;width:70px;height:70px;border-color:var(--gold);border-style:solid}
.corner.tl{left:150px;top:302px;border-width:4px 0 0 4px}
.corner.br{left:990px;top:672px;border-width:0 4px 4px 0}
.testi-photo{left:190px;top:344px;width:340px;height:380px;background:linear-gradient(170deg,#9eb7cc,#c8d6e2 45%,#7f8c97)}
.testi-body{left:580px;top:390px;width:440px;color:var(--white)}
.stars{color:var(--gold);font-size:26px;letter-spacing:4px;margin-bottom:20px}
.testi-body p{font-size:19px;line-height:1.55;color:#e5e5e5;margin-bottom:28px}
.testi-body .name{font-weight:700;font-size:17px;letter-spacing:1px}
.quote-mark{left:965px;top:640px;font-size:90px;font-weight:800;color:#6b6b6b;line-height:1}
.round-arrow{width:46px;height:46px;border-radius:50%;background:linear-gradient(135deg,var(--gold-dark),var(--gold-light));display:flex;align-items:center;justify-content:center;position:absolute}

/* Projects */
.projects{height:650px;background:var(--white)}
.projects .section-title{position:absolute;left:100px;top:58px;color:var(--ink);text-align:left}
.projects .section-title span{color:var(--gold)}
.project-photo{top:160px;height:410px}
.project-caption{position:absolute;left:348px;top:470px;width:520px;height:100px;background:linear-gradient(180deg,rgba(0,0,0,0),rgba(0,0,0,.8));color:var(--white);text-align:center;padding-top:34px}
.project-caption h3{font-size:20px;font-weight:800;letter-spacing:1px}
.project-caption p{font-size:13px;color:#ddd;margin-top:4px}

/* Contact */
.contact{height:580px;background:var(--white)}
.contact-left{left:0;top:0;width:600px;height:580px;background:#161616;color:var(--white);padding:84px 0 0 144px}
.eyebrow{font-size:17px;font-weight:500;letter-spacing:1px;color:#ddd}
.contact-left h2{font-size:44px;font-weight:800;margin:6px 0 26px}
.contact-left h2 span{color:var(--gold)}
.contact-left .lead{font-size:16px;line-height:1.5;color:#cfcfcf;width:400px;margin-bottom:34px}
.contact-item{display:flex;align-items:center;gap:18px;margin-bottom:22px;font-size:16px;line-height:1.35}
.contact-item .ico{width:48px;height:48px;border-radius:50%;background:linear-gradient(135deg,var(--gold-dark),var(--gold-light));display:flex;align-items:center;justify-content:center;flex:none}
.contact-item strong{font-weight:700;display:block}
.contact-right{left:600px;top:0;width:600px;height:580px;background:linear-gradient(135deg,#c29b38,#e7cb72 55%,#c9a33e)}
.contact-right h2{position:absolute;left:80px;top:100px;font-size:30px;font-weight:700;color:var(--white);letter-spacing:1px}
.field{position:absolute;background:var(--white);height:46px;font-size:14px;color:#555;padding:12px 16px}
.send-btn{position:absolute;left:80px;top:448px;background:var(--ink);color:var(--white);font-weight:700;font-size:15px;padding:13px 26px;border-radius:26px}

/* Footer */
.site-footer{height:382px;background:var(--white)}
.foot-brand{left:90px;top:80px;font-size:34px;font-weight:800;color:var(--ink);letter-spacing:2px}
.foot-col{top:66px;border-left:4px solid var(--gold);padding-left:16px}
.foot-col h4{font-size:17px;font-weight:800;color:var(--ink);letter-spacing:1px;margin-bottom:10px}
.foot-col li{list-style:none;font-size:16px;line-height:1.55;color:var(--text)}
.foot-contact li{display:flex;align-items:center;gap:10px;margin-bottom:6px}
.mini-ico{width:26px;height:26px;border-radius:50%;background:var(--gold);flex:none}
.social{display:flex;gap:10px}
.social span{width:32px;height:32px;border-radius:50%;background:var(--gold);display:block}
.foot-rule{left:90px;top:300px;width:1020px;height:1px;background:#d8d8d8}
.copyright{left:0;top:322px;width:1200px;text-align:center;font-size:14px;color:var(--text)}
.back-top{left:980px;top:322px;font-size:14px;color:var(--text)}
</style>
</head>
<body>

<header class="hero">
  <div class="photo hero-photo" role="img" aria-label="Engineers in hard hats and safety vests reviewing a building under construction with scaffolding"></div>
  <div class="abs hero-shade"></div>
  <div class="abs brand">KESTRADA<span class="brand-mark"></span></div>
  <nav class="abs nav">
    <a class="active" href="#">HOME</a>
    <a href="#">ABOUT US</a>
    <a href="#">SERVICES</a>
    <a href="#">PROJECTS</a>
    <a href="#">CONTACT US</a>
  </nav>
  <div class="abs phone-pill">
    <svg width="18" height="18" viewBox="0 0 24 24"><path fill="#151515" d="M6.6 10.8a15.1 15.1 0 0 0 6.6 6.6l2.2-2.2c.3-.3.7-.4 1-.2 1.1.4 2.3.6 3.6.6.6 0 1 .4 1 1V20c0 .6-.4 1-1 1A17 17 0 0 1 3 4c0-.6.4-1 1-1h3.5c.6 0 1 .4 1 1 0 1.3.2 2.5.6 3.6.1.3 0 .7-.2 1z"/></svg>
    (+1 555) 204 7731
  </div>
  <svg class="abs" style="left:330px;top:160px" width="540" height="170" viewBox="0 0 540 170">
    <path d="M30 2 H2 V60" fill="none" stroke="#c9a33e" stroke-width="4"/>
    <path d="M510 168 H538 V110" fill="none" stroke="#c9a33e" stroke-width="4"/>
  </svg>
  <h1 class="abs hero-title"><span class="gold">BUILDING WITH INTEGRITY.</span><br><span class="white">SERVING WITH PURPOSE.</span></h1>
  <p class="abs hero-sub">Construction and remediation services you can trust.</p>
  <div class="abs hero-cta"><span class="btn-gold">CONTACT US</span></div>
  <svg class="abs hero-curve" width="1200" height="220" viewBox="0 0 1200 220">
    <defs>
      <linearGradient id="heroGold" x1="0" x2="1">
        <stop offset="0" stop-color="#a9822a"/><stop offset=".5" stop-color="#e6c869"/><stop offset="1" stop-color="#a9822a"/>
      </linearGradient>
    </defs>
    <path d="M0 60 Q600 220 1200 40 V220 H0 Z" fill="url(#heroGold)"/>
    <path d="M0 86 Q600 250 1200 70 V220 H0 Z" fill="#ffffff"/>
  </svg>
</header>

<section class="about">
  <div class="photo about-photo" role="img" aria-label="Two construction workers in hard hats on a rebar-filled building site"></div>
  <div class="abs about-badge" role="img" aria-label="Veteran-owned business certification badge"></div>
  <div class="abs about-body">
    <h2>ABOUT <span>KESTRADA</span></h2>
    <p>Lorem ipsum dolor sit amet, consectetur adipiscing elit, sed do eiusmod tempor incididunt ut labore et dolore magna aliqua. Quis ipsum suspendisse ultrices gravida. Risus commodo viverra maecenas accumsan lacus vel facilisis. Lorem ipsum dolor sit amet conse</p>
    <p class="quote-block">Ancididunt ut labore et dolore magna aliqua. Quis ipsum suspendisse ultrices gravida. Risus commodo viverra maecenas accumsan lacus vel facilisis.</p>
    <span class="btn-gold">LEARN MORE</span>
  </div>
</section>

<section class="services">
  <h2 class="section-title">OUR SERVICES</h2>
  <div class="title-rule"></div>
  <div class="service-card" style="left:48px">
    <div class="photo" style="inset:0;background:linear-gradient(160deg,#8c8a86,#c3b8a4 60%,#6b5a3d)" role="img" aria-label="Contractors shaking hands over site plans"></div>
    <div class="shade"></div>
    <h3>GENERAL<br>CONTRACTING</h3>
  </div>
  <div class="service-feature">
    <div class="feature-icon">
      <svg width="48" height="48" viewBox="0 0 24 24" fill="none" stroke="#151515" stroke-width="1.6"><path d="M4 20h16M6 20V10l6-5 6 5v10M10 20v-5h4v5"/></svg>
    </div>
    <h3>DESIGN-BUILD<br>CONSTRUCTION</h3>
    <p>Lorem ipsum dolor sit amet, consectetur adipiscing elit, sed do eiusmod tempor incididunt ut labore et dolore magna aliqua.</p>
    <span class="btn-gold">LEARN MORE</span>
  </div>
  <div class="service-card" style="left:600px">
    <div class="photo" style="inset:0;background:linear-gradient(165deg,#7d7a73,#a79a86 50%,#5b5147)" role="img" aria-label="Crew in orange uniforms clearing storm debris"></div>
    <div class="shade"></div>
    <h3>DISASTER RECOVERY</h3>
  </div>
  <div class="service-card" style="left:888px">
    <div class="photo" style="inset:0;background:linear-gradient(165deg,#9fb9a1,#5f8a4e 55%,#3f5d32)" role="img" aria-label="Field worker taking environmental samples in a green field"></div>
    <div class="shade"></div>
    <h3>ENVIRONMENTAL<br>REMEDIATION</h3>
  </div>
</section>

<section class="testimonials">
  <div class="abs testi-bg"></div>
  <svg class="abs" style="left:0;top:0" width="1200" height="200" viewBox="0 0 1200 200">
    <defs>
      <linearGradient id="chevGold" x1="0" x2="1">
        <stop offset="0" stop-color="#a9822a"/><stop offset=".5" stop-color="#e6c869"/><stop offset="1" stop-color="#a9822a"/>
      </linearGradient>
    </defs>
    <path d="M0 0 H1200 V40 L600 130 L0 40 Z" fill="url(#chevGold)"/>
    <path d="M0 0 H1200 V22 L600 104 L0 22 Z" fill="#c9a33e"/>
  </svg>
  <h2 class="section-title">WHAT <span>CLIENT SAYS</span></h2>
  <div class="abs corner tl"></div>
  <div class="abs testi-card"></div>
  <div class="abs corner br"></div>
  <div class="photo testi-photo" role="img" aria-label="Modern glass office building against a blue sky"></div>
  <div class="abs testi-body">
    <div class="stars">★★★★★</div>
    <p>“Lorem ipsum dolor sit amet, consectetur adipiscing elit, sed do eiusmod tempor incididunt ut labore et dolore magna aliqua. Quis ipsum suspendisse ultrices gravida. Risus commodo viverra maecenas accumsan lacus vel facilisis.”</p>
    <div class="name">DANA WHITLOW</div>
  </div>
  <div class="abs quote-mark">”</div>
  <div class="round-arrow" style="left:556px;top:758px"><svg width="20" height="20" viewBox="0 0 24 24"><path d="M15 5l-7 7 7 7" fill="none" stroke="#151515" stroke-width="2.5"/></svg></div>
  <div class="round-arrow" style="left:612px;top:758px"><svg width="20" height="20" viewBox="0 0 24 24"><path d="M9 5l7 7-7 7" fill="none" stroke="#151515" stroke-width="2.5"/></svg></div>
</section>

<section class="projects">
  <h2 class="section-title">RECENT <span>PROJECTS</span></h2>
  <div class="round-arrow" style="left:988px;top:62px"><svg width="20" height="20" viewBox="0 0 24 24"><path d="M15 5l-7 7 7 7" fill="none" stroke="#151515" stroke-width="2.5"/></svg></div>
  <div class="round-arrow" style="left:1048px;top:62px"><svg width="20" height="20" viewBox="0 0 24 24"><path d="M9 5l7 7-7 7" fill="none" stroke="#151515" stroke-width="2.5"/></svg></div>
  <div class="photo project-photo" style="left:100px;width:232px;background:linear-gradient(160deg,#a06a3e,#c89063 50%,#6c4a30)" role="img" aria-label="Timber framing of a house under construction"></div>
  <div class="photo project-photo" style="left:348px;width:520px;background:linear-gradient(170deg,#8fb1d0,#c7d8e6 45%,#5d7184)" role="img" aria-label="Completed modern glass office towers"></div>
  <div class="project-caption"><h3>PROJECT HEADING</h3><p>Lorem ipsum dolor sit amet consectetur adipisc</p></div>
  <div class="photo project-photo" style="left:882px;width:238px;background:linear-gradient(165deg,#9ab3cf,#b57b55 55%,#7a5038)" role="img" aria-label="Brick apartment building wrapped in scaffolding"></div>
</section>

<section class="contact">
  <div class="abs contact-left">
    <div class="eyebrow">GET IN TOUCH</div>
    <h2>CONTACT <span>US</span></h2>
    <p class="lead">Lorem ipsum dolor sit amet, consectetur adipiscing elit, sed do eiusmod tempor.</p>
    <div class="contact-item">
      <span class="ico"><svg width="22" height="22" viewBox="0 0 24 24"><path fill="#151515" d="M12 2a7 7 0 0 0-7 7c0 5 7 13 7 13s7-8 7-13a7 7 0 0 0-7-7zm0 9.5A2.5 2.5 0 1 1 12 6.5a2.5 2.5 0 0 1 0 5z"/></svg></span>
      <div>2480 Harbor Point Rd.,<br>Coral Bend, FL 33402</div>
    </div>
    <div class="contact-item">
      <span class="ico"><svg width="20" height="20" viewBox="0 0 24 24"><path fill="#151515" d="M6.6 10.8a15.1 15.1 0 0 0 6.6 6.6l2.2-2.2c.3-.3.7-.4 1-.2 1.1.4 2.3.6 3.6.6.6 0 1 .4 1 1V20c0 .6-.4 1-1 1A17 17 0 0 1 3 4c0-.6.4-1 1-1h3.5c.6 0 1 .4 1 1 0 1.3.2 2.5.6 3.6.1.3 0 .7-.2 1z"/></svg></span>
      <div><strong>Phone Number</strong>+1 (555) 204 7731</div>
    </div>
    <div class="contact-item">
      <span class="ico"><svg width="22" height="22" viewBox="0 0 24 24"><path fill="none" stroke="#151515" stroke-width="2" d="M3 6h18v12H3zM3 6l9 7 9-7"/></svg></span>
      <div><strong>Email address</strong>enquiry@kestrada.com</div>
    </div>
  </div>
  <div class="abs contact-right">
    <h2>LEAVE US A MESSAGE</h2>
    <div class="field" style="left:80px;top:176px;width:212px">First Name</div>
    <div class="field" style="left:308px;top:176px;width:212px">Last Name</div>
    <div class="field" style="left:80px;top:234px;width:440px">Email address</div>
    <div class="field" style="left:80px;top:292px;width:440px">Phone Number</div>
    <div class="field" style="left:80px;top:350px;width:440px;height:82px">Leave Message</div>
    <div class="send-btn">SEND MESSAGE ›</div>
  </div>
</section>

<footer class="site-footer">
  <div class="abs foot-brand">KESTRADA<span class="brand-mark"></span></div>
  <div class="abs foot-col" style="left:340px">
    <h4>NAVIGATION</h4>
    <ul><li>Home</li><li>About Us</li><li>Services</li><li>Projects</li><li>Contact Us</li></ul>
  </div>
  <div class="abs foot-col foot-contact" style="left:550px">
    <h4>CONTACT US</h4>
    <ul>
      <li><span class="mini-ico"></span>2480 Harbor Point Rd., Coral Bend</li>
      <li><span class="mini-ico"></span>+1 (555) 204 7731</li>
      <li><span class="mini-ico"></span>enquiry@kestrada.com</li>
    </ul>
  </div>
  <div class="abs foot-col" style="left:910px">
    <h4>FOLLOW US</h4>
    <div class="social"><span></span><span></span><span></span></div>
  </div>
  <div class="abs foot-rule"></div>
  <div class="abs copyright">Copyright © 2025 KESTRADA. All Right Reserved</div>
  <div class="abs back-top">Back to Top ↑</div>
</footer>

</body>
</html>
```